Business Card Design Project

Business Card
We are rebranding with a new logo
Industry/Entity Type
Business
Contact Information for Business Card
Dennis Morvale +61 487215963 dennis@quorv.com.au P.O. Box 872 Fernlow QLD 4309
Requirements
Must have
- Logo

```html
<!DOCTYPE html>
<html lang="en">
<head>
<meta charset="utf-8">
<title>Quorv International – Business Card</title>
<link href="https://fonts.googleapis.com/css2?family=Open+Sans:wght@400;600;700&display=swap" rel="stylesheet">
<style>
  :root {
    --backdrop: #2b2b2d;
    --card-white: #f7f7f5;
    --brand-orange: #ec8a1f;
    --brand-orange-light: #f39a2e;
    --brand-blue: #1a8fc0;
    --brand-blue-deep: #0f6f9c;
    --ink: #3a3a3a;
    --rule: #8a8a8a;
    --on-orange: #ffffff;
  }
  * { box-sizing: border-box; margin: 0; padding: 0; }
  html, body { width: 1200px; height: 960px; overflow: hidden; }
  body {
    background: var(--backdrop);
    font-family: "Open Sans", Arial, sans-serif;
    position: relative;
  }
  .card {
    position: absolute;
    left: 220px;
    width: 760px;
    height: 430px;
    overflow: hidden;
  }
  .card--back {
    top: 35px;
    background: linear-gradient(135deg, var(--brand-orange-light), var(--brand-orange));
    display: flex;
    flex-direction: column;
    align-items: center;
    justify-content: center;
    color: var(--on-orange);
  }
  .card--back .brand-name {
    font-size: 46px;
    font-weight: 600;
    letter-spacing: 3px;
    color: var(--on-orange);
  }
  .card--back .web {
    margin-top: 40px;
    font-size: 17px;
    letter-spacing: 4px;
    color: var(--on-orange);
  }
  .card--front {
    top: 495px;
    background: var(--card-white);
  }
  .front-swoosh { position: absolute; left: 0; top: 0; }
  .front-brand {
    position: absolute;
    right: 50px;
    top: 95px;
    font-size: 30px;
    font-weight: 600;
    letter-spacing: 2px;
    color: var(--brand-blue);
  }
  .holder {
    position: absolute;
    left: 48px;
    top: 138px;
    font-size: 20px;
    font-weight: 700;
    color: var(--brand-blue);
    letter-spacing: 0.5px;
  }
  .rule {
    position: absolute;
    height: 1px;
    background: var(--rule);
  }
  .rule--name { left: 48px; right: 40px; top: 170px; }
  .rule--address { left: 470px; right: 40px; top: 292px; }
  .contacts {
    position: absolute;
    left: 48px;
    top: 180px;
    list-style: none;
    font-size: 17px;
    color: var(--ink);
    line-height: 25px;
  }
  .contacts li { display: flex; align-items: center; gap: 10px; }
  .contacts svg { width: 14px; height: 14px; fill: var(--brand-blue-deep); }
  .address {
    position: absolute;
    right: 45px;
    top: 302px;
    text-align: right;
    font-size: 19px;
    line-height: 24px;
    color: var(--ink);
  }
</style>
</head>
<body>
  <section class="card card--back">
    <div class="brand-name">QUORV INTERNATIONAL</div>
    <div class="web">www.quorv.com.au</div>
  </section>

  <section class="card card--front">
    <svg class="front-swoosh" width="760" height="430" viewBox="0 0 760 430" aria-hidden="true">
      <path d="M0 240 C 120 330, 380 360, 760 430 L 0 430 Z" fill="var(--brand-orange)"/>
      <path d="M0 255 C 130 345, 390 370, 760 440 L 760 430 L 0 430 Z" fill="var(--card-white)"/>
      <path d="M0 262 C 140 355, 400 378, 760 448 L 760 430 L 0 430 Z" fill="var(--brand-blue)"/>
      <path d="M0 300 C 180 390, 420 392, 760 460 L 760 430 L 0 430 Z" fill="var(--brand-blue-deep)" opacity="0.55"/>
    </svg>

    <div class="front-brand">QUORV INTERNATIONAL</div>

    <div class="holder">DENNIS MORVALE</div>
    <div class="rule rule--name"></div>

    <ul class="contacts">
      <li>
        <svg viewBox="0 0 16 16" aria-hidden="true"><path d="M3 1h3l1.5 4-2 1.3a9 9 0 0 0 4.2 4.2L11 8.5l4 1.5v3a2 2 0 0 1-2 2A12 12 0 0 1 1 3a2 2 0 0 1 2-2z"/></svg>
        <span>+61 487215963</span>
      </li>
      <li>
        <svg viewBox="0 0 16 16" aria-hidden="true"><path d="M1 3h14v10H1z M1 3l7 6 7-6" stroke="var(--card-white)" stroke-width="1"/></svg>
        <span>dennis@quorv.com.au</span>
      </li>
      <li>
        <svg viewBox="0 0 16 16" aria-hidden="true"><circle cx="8" cy="8" r="7"/><path d="M1 8h14M8 1c3 3 3 11 0 14M8 1c-3 3-3 11 0 14" stroke="var(--card-white)" stroke-width="1" fill="none"/></svg>
        <span>www.quorv.com.au</span>
      </li>
    </ul>

    <div class="rule rule--address"></div>
    <div class="address">
      <div>P.O. Box 872</div>
      <div>Fernlow QLD 4309</div>
    </div>
  </section>
</body>
</html>
```